Logo and Website Design for QR.KA Horizon - a Software Engineering and IT company

Software engineering and IT are two different disciplines - and yet inseparably linked. At QR.KA Horizon, we combine both worlds and ensure that our software solutions are not only innovative and powerful, but also integrate perfectly into existing IT landscapes. Vision stands more for imagination, so it is not neccessary something what has to do with visualisation. Please consider that the winning competitor is also instructed to make a logo for the company. So please make a suitable logo for QR.KA Horizon to which the website fits to and show it during the website creation process. A good Logo desing is important for winning the competition. The website should contain a landing page with inspiring, perhaps futuristic photos of a datacenter and lines of code. Eventuelly flewent integrated in the text. On the landing page the company should introduced with a small text (max 250 words) followed by a section with a short text to one of our products nearby a graphic visualising the architecture of the product. The menue should be on top and fixed during scrolling and consist of the menue items home, solutions, who are we and a contact button. There should be a footer for linking social media, rights and Impressum. Only as an idea not a must. The very first view on the landing page could also be the menue bar and below of it a transparent unsharp photo (e.g. datacenter, lines of code, both ;) with the company name in the center.

###############################################################

Hi Designers,

Despite your very good approaches for describing QR.KA Horizon, here a short introduction (german text) from ourself:

------
QR.KA Horizon – Ihr Partner für ganzheitliche Softwarelösungen

Die QR.KA Horizon ist ein dynamisches Unternehmen, das sich nicht nur auf die Konzeption, das Design und die Entwicklung maßgeschneiderter Software spezialisiert hat, sondern auch deren reibungslosen Betrieb sicherstellt. Mit einem Team aus erfahrenen Softwarearchitekten und IT-Professionals verbinden wir modernste Softwareentwicklung mit tiefgehendem IT-Know-how – für Lösungen, die nachhaltig, leistungsstark und zukunftssicher sind.

Software Engineering trifft IT – Perfektion in Kombination
Software Engineering und IT sind zwei unterschiedliche Disziplinen – und doch untrennbar miteinander verbunden. Wir bei QR.KA Horizon vereinen beide Welten und sorgen dafür, dass unsere Softwarelösungen nicht nur innovativ und leistungsfähig sind, sondern sich auch perfekt in bestehende IT-Landschaften integrieren.

Expertise mit Fokus auf Healthcare & komplexe IT-Umgebungen
Unsere Experten bringen jahrzehntelange Erfahrung aus dem Healthcare-Sektor mit und unterstützen IT-Abteilungen großer Kliniken in der Entwicklung und Optimierung von Softwarelösungen. Von Anwendungssoftware bis hin zu Steuerungssystemen – unsere Softwareingenieure wissen genau, worauf es ankommt.

Ganzheitlicher Ansatz – über die Software hinaus
Wir entwickeln nicht nur Software, sondern übernehmen auch die Verantwortung für deren stabile und effiziente Betriebsumgebung. Egal, ob on-premises, in der Cloud oder als SaaS-Lösung – wir kümmern uns um den kompletten Lifecycle Ihrer Anwendung.

Ihre Vision – unsere Mission.
Ob Neuentwicklung einer SaaS-Anwendung oder die Migration bestehender Lösungen in eine moderne SaaS-Umgebung – mit QR.KA Horizon haben Sie einen starken Partner an Ihrer Seite.

Lassen Sie uns gemeinsam die Zukunft Ihrer Software gestalten!
--------------

Our first solution called "Clear Record Transfer Gateway" (CLURA)
-------------------
Teilen Sie Ihre Daten sicher – ohne Kompromisse!

Sie nutzen eine relationale Datenbank (Brightcask, Tabulon Hub, Vellumdb etc.) und möchten ausgewählte Daten mit Dritten teilen – sei es für ein Data Warehouse, Business Controller, Lieferanten oder Kunden? Doch dabei sollen Datensicherheit, Integrität und Verfügbarkeit Ihrer primären Lösung in keiner Weise gefährdet werden?

Mit unserer Lösung erhalten Sie genau das: Maximalen Schutz für Ihre Anwendung bei gleichzeitigem Nutzen durch autorisierte Dritte – ganz ohne teure Lizenzkosten für eine Schattendatenbank.

Lassen Sie uns gemeinsam herausfinden, wie Sie Ihre Daten sicher und effizient nutzen können. Kontaktieren Sie uns – wir zeigen Ihnen, was möglich ist!
---------------------

Our second solution MIVO:
---------------------
MIVO – Program for a Tone Matching Instrument ist die smarte Lösung für Unternehmen, die bei Farbgenauigkeit keine Kompromisse machen. Die Software erkennt Farbabweichungen zwischen Mustern vollautomatisch, beschreibt sie verständlich und sorgt so für gleichbleibend hohe Produktqualität – schnell, visuell und präzise. Perfekt für alle, die Farbe zur Vertrauenssache machen.
-------------------------

Thanks,
Gerold

Target Market(s)

IT Professionals from any sector

Industry/Entity Type

Healthcare and other

Coding

Coded - Design and coding required

Number of Pages Required

1 page

Font styles to use
Sans Serif

Colors
0054AA
0677BA
7BADD7
CADEEF
E8F1F8
0094D4
00A9DD
6FCCEA
C7EBF8
E9F6FB
00AB8E
00BBA5
67D7C9
C6EFE9
E9F9F6

Requirements
Must have
• Please see description
Nice to have
• On the landing page the company should introduced with a small text (max 250 words) followed by a section with a short text to one of our products nearby a graphic visualising the architecture of the product. The menue should be on top and fixed during scrolling and consist of the menue items home, solutions, who are we and a contact button. There should be a footer for linking social media, rights and Impressum. Only as an idea not a must. The very first view on the landing page could also be the menue bar and below of it a transparent unsharp photo (e.g. datacenter, lines of code, both ;) with the company name in the center.
Should not have
• Please see description

```html
<!DOCTYPE html>
<html lang="en">
<head>
<meta charset="utf-8">
<title>QR.KA Horizon</title>
<link href="https://fonts.googleapis.com/css2?family=Lato:wght@400;700;900&display=swap" rel="stylesheet">
<style>
:root{
  --blue:#0094D4;
  --blue-deep:#0677BA;
  --blue-dark:#0054AA;
  --ink:#1e1e1e;
  --text:#3a3a3a;
  --grey-bg:#efefef;
  --footer:#1b1b1d;
  --star:#f08a1c;
  --white:#fff;
}
*{box-sizing:border-box;margin:0;padding:0}
html,body{width:1200px;height:3737px;overflow:hidden}
body{position:relative;font-family:'Lato',sans-serif;color:var(--text);background:var(--white)}
.accent{color:var(--blue)}
.section-title{position:absolute;left:0;width:1200px;text-align:center;font-size:44px;font-weight:700;color:var(--ink)}

/* header */
.site-header{position:absolute;top:0;left:0;width:1200px;height:120px;z-index:5}
.brand{position:absolute;left:112px;top:38px;display:flex;align-items:center;gap:18px;color:var(--white);font-weight:700;font-size:36px;letter-spacing:.5px}
.brand-mark{width:46px;height:46px;border-radius:50%;background:var(--white)}
.nav{position:absolute;left:563px;top:42px;display:flex;gap:12px;align-items:center}
.nav a{color:var(--white);text-decoration:none;font-size:15px;padding:7px 9px;border-radius:2px}
.nav a.active{background:var(--blue)}
.btn{display:inline-block;background:var(--blue);color:var(--white);font-weight:700;font-size:16px;text-decoration:none;text-align:center;border-radius:2px}
.btn-start{position:absolute;left:950px;top:37px;width:137px;height:42px;line-height:42px}

/* hero */
.hero{position:absolute;top:0;left:0;width:1200px;height:740px;overflow:hidden}
.hero-photo{position:absolute;inset:0;
  background:
    radial-gradient(ellipse 260px 180px at 520px 560px,rgba(70,90,110,.55),transparent 70%),
    radial-gradient(ellipse 200px 160px at 760px 560px,rgba(60,80,100,.5),transparent 70%),
    radial-gradient(ellipse 120px 260px at 70px 420px,rgba(40,190,120,.35),transparent 70%),
    radial-gradient(ellipse 140px 240px at 1140px 300px,rgba(60,170,210,.3),transparent 70%),
    radial-gradient(ellipse 180px 140px at 200px 230px,rgba(90,200,230,.28),transparent 70%),
    radial-gradient(ellipse 170px 300px at 1030px 470px,rgba(140,110,90,.35),transparent 70%),
    linear-gradient(180deg,#0d1a26 0%,#15283a 40%,#1a2330 70%,#0e141b 100%)}
.hero-shade{position:absolute;inset:0;background:radial-gradient(ellipse at 50% 40%,rgba(0,0,0,.05),rgba(0,0,0,.45) 100%)}
.hero-title{position:absolute;top:165px;width:1200px;text-align:center;font-size:80px;font-weight:700;color:var(--white);letter-spacing:-1px}
.hero-sub{position:absolute;top:272px;left:300px;width:600px;text-align:center;font-size:22px;line-height:32px;color:var(--white)}
.btn-hero{position:absolute;left:494px;top:363px;width:206px;height:40px;line-height:40px;font-size:16px}
.dots{position:absolute;top:670px;left:564px;display:flex;gap:8px}
.dots i{width:12px;height:12px;border-radius:50%;background:rgba(255,255,255,.45)}
.dots i:first-child{background:var(--white)}
.hero-wave{position:absolute;left:0;top:600px}

/* products */
.products-title{top:810px}
.arrow{position:absolute;top:975px;width:33px;height:33px}
.product{position:absolute;top:892px;width:308px}
.product-img{height:189px;border-radius:2px}
.product-img.a{background:
    radial-gradient(ellipse 90px 60px at 165px 85px,rgba(120,220,255,.85),transparent 70%),
    radial-gradient(ellipse 200px 60px at 150px 170px,rgba(0,160,230,.6),transparent 70%),
    linear-gradient(160deg,#061a3a 0%,#0b4c8c 50%,#04264f 100%)}
.product-img.b{background:
    radial-gradient(circle 60px at 130px 105px,rgba(80,220,255,.9),rgba(0,120,200,.4) 55%,transparent 80%),
    radial-gradient(ellipse 80px 120px at 250px 60px,rgba(60,80,110,.7),transparent 70%),
    linear-gradient(135deg,#03101f 0%,#0b3560 50%,#04101f 100%)}
.product-img.c{background:
    radial-gradient(ellipse 120px 60px at 160px 110px,rgba(230,170,140,.55),transparent 70%),
    radial-gradient(ellipse 160px 50px at 180px 170px,rgba(40,50,60,.8),transparent 70%),
    linear-gradient(135deg,#d3dbe4 0%,#95a5b6 50%,#3b4656 100%)}
.product-head{display:flex;align-items:center;gap:22px;margin-top:26px}
.product-icon{flex:none;width:43px;height:43px;background:var(--blue);border-radius:4px;display:flex;align-items:center;justify-content:center}
.product-name{font-size:21px;font-weight:700;color:var(--ink)}
.product-text{margin-top:20px;font-size:14.5px;line-height:22px;color:var(--text)}
.product-line{position:absolute;top:373px;left:3px;height:2px;background:var(--blue)}

/* about */
.about{position:absolute;top:1340px;left:0;width:1200px;height:681px;overflow:hidden;
  background:linear-gradient(90deg,#c9cfd6 0%,#a9b6c3 35%,#5d98c0 52%,#1f86c0 62%,#0a7cb8 100%)}
.about-photo{position:absolute;left:0;top:0;width:700px;height:681px;
  background:
    radial-gradient(ellipse 110px 140px at 150px 250px,rgba(225,190,160,.6),transparent 70%),
    radial-gradient(ellipse 90px 120px at 390px 150px,rgba(110,80,60,.55),transparent 70%),
    radial-gradient(ellipse 100px 130px at 470px 330px,rgba(100,72,55,.55),transparent 70%),
    radial-gradient(ellipse 140px 170px at 130px 420px,rgba(170,180,195,.7),transparent 70%),
    radial-gradient(ellipse 240px 70px at 360px 600px,rgba(150,120,90,.6),transparent 70%),
    radial-gradient(ellipse 160px 120px at 440px 470px,rgba(40,60,90,.55),transparent 70%),
    linear-gradient(90deg,rgba(220,224,230,1) 0%,rgba(185,195,206,.9) 60%,rgba(120,160,195,0) 100%)}
.about-cap{position:absolute;top:0;left:0}
.about h2{position:absolute;left:647px;top:110px;font-size:43px;font-weight:700;color:var(--white)}
.about-copy{position:absolute;left:645px;top:182px;width:445px;color:var(--white);font-size:14.5px;line-height:25.8px}
.about-copy p+p{margin-top:19px}
.btn-dark{position:absolute;left:646px;top:565px;width:145px;height:41px;line-height:41px;background:#1f1f1f;color:var(--white);font-weight:700;font-size:15px;text-align:center;text-decoration:none;border-radius:2px}

/* testimonials */
.testimonials{position:absolute;top:2021px;left:0;width:1200px;height:560px;background:var(--grey-bg)}
.testimonials .section-title{top:76px}
.quote{position:absolute;top:170px;width:317px;height:227px;background:#faf9f7;border:1px solid #e2e2e2;border-radius:3px;padding:28px 22px}
.quote.featured{background:var(--blue);border-color:var(--blue)}
.stars{color:var(--star);font-size:16px;letter-spacing:1px}
.featured .stars{color:var(--white)}
.quote p{margin-top:14px;font-size:14.5px;line-height:22px;color:#555}
.quote h4{margin-top:17px;font-size:18px;font-weight:700;color:var(--ink)}
.quote time{display:block;margin-top:10px;font-size:13px;color:#555}
.featured p,.featured h4,.featured time{color:var(--white)}
.t-dots{position:absolute;top:422px;left:577px;display:flex;gap:4px}
.t-dots i{width:13px;height:5px;border-radius:3px;background:#c9c9c9}
.t-dots i:first-child{background:var(--blue)}
.t-wave{position:absolute;left:0;top:430px}

/* solutions */
.solutions-title{position:absolute;left:113px;top:2652px;font-size:44px;font-weight:700;color:var(--ink)}
.solutions-sub{position:absolute;left:112px;top:2731px;font-size:18px;font-weight:700;color:var(--blue)}
.solutions-copy{position:absolute;left:112px;top:2776px;width:445px;font-size:14.5px;line-height:25.8px}
.btn-sol{position:absolute;left:112px;top:2996px;width:146px;height:41px;line-height:41px}
.sol-photo{position:absolute;left:656px;top:2630px;width:430px;height:430px;border-radius:50%;
  box-shadow:-7px 7px 0 var(--blue);
  background:
    radial-gradient(ellipse 110px 90px at 300px 160px,rgba(240,235,225,.8),transparent 70%),
    radial-gradient(ellipse 70px 90px at 120px 230px,rgba(90,60,45,.7),transparent 70%),
    radial-gradient(ellipse 70px 90px at 290px 240px,rgba(170,120,90,.6),transparent 70%),
    radial-gradient(ellipse 180px 60px at 220px 330px,rgba(200,190,175,.8),transparent 70%),
    radial-gradient(ellipse 90px 200px at 40px 180px,rgba(40,40,45,.8),transparent 70%),
    linear-gradient(160deg,#6d6259 0%,#a79585 45%,#5b5049 75%,#2e2a28 100%)}

/* footer */
.footer{position:absolute;top:3150px;left:0;width:1200px;height:587px;background:var(--footer);color:var(--white)}
.footer-cap{position:absolute;top:0;left:0}
.footer-brand{position:absolute;left:0;width:1200px;top:125px;display:flex;justify-content:center;align-items:center;gap:20px;font-size:40px;font-weight:700}
.footer-brand .brand-mark{width:56px;height:56px;background:var(--blue)}
.fcol{position:absolute;top:233px}
.fcol h3{font-size:21px;font-weight:700;margin-bottom:22px}
.fcol p,.fcol a{display:block;color:var(--white);text-decoration:none;font-size:15px;line-height:26px}
.links a{margin-bottom:21px}
.contact-row{display:flex;gap:22px;margin-bottom:20px}
.contact-row svg{flex:none;margin-top:4px}
.social{position:absolute;left:112px;top:420px;display:flex;gap:8px;align-items:center}
.social a{font-size:12px;color:var(--white);text-decoration:none;padding:6px 8px;border:1px solid #555;border-radius:3px}
.social a:first-child{background:var(--blue);border-color:var(--blue)}
.rule{position:absolute;left:112px;top:545px;width:976px;height:1px;background:#3a3a3a}
.copyright{position:absolute;top:558px;left:0;width:1200px;text-align:center;font-size:13px}
</style>
</head>
<body>

<section class="hero">
  <div class="hero-photo" role="img" aria-label="Engineers at monitors showing lines of code inside a datacenter with glowing server racks"></div>
  <div class="hero-shade"></div>
  <h1 class="hero-title">QR.KA HORIZON</h1>
  <p class="hero-sub">Bridging the gap between software engineering and IT to create powerful, future-ready solutions.</p>
  <a class="btn btn-hero" href="#">Schedule a Consultation</a>
  <div class="dots"><i></i><i></i><i></i><i></i></div>
  <svg class="hero-wave" width="1200" height="140" viewBox="0 0 1200 140">
    <path d="M0 28 Q600 190 1200 20 L1200 140 L0 140Z" fill="var(--blue)"/>
    <path d="M0 24 Q600 150 1200 18 L1200 140 L0 140Z" fill="#fff" transform="translate(0,6)"/>
  </svg>
</section>

<header class="site-header">
  <div class="brand"><span class="brand-mark"></span>QR.KA HORIZON</div>
  <nav class="nav">
    <a class="active" href="#">Home</a>
    <a href="#">Solutions</a>
    <a href="#">Who Are We</a>
    <a href="#">Contact</a>
  </nav>
  <a class="btn btn-start" href="#">Get Started</a>
</header>

<h2 class="section-title products-title">Our <span class="accent">Products</span></h2>
<svg class="arrow" style="left:58px" viewBox="0 0 33 33"><circle cx="16.5" cy="16.5" r="16.5" fill="var(--blue)"/><path d="M19 10l-6 6.5 6 6.5" stroke="#fff" stroke-width="2.5" fill="none"/></svg>
<svg class="arrow" style="left:1108px" viewBox="0 0 33 33"><circle cx="16.5" cy="16.5" r="16.5" fill="var(--blue)"/><path d="M14 10l6 6.5-6 6.5" stroke="#fff" stroke-width="2.5" fill="none"/></svg>

<article class="product" style="left:112px">
  <div class="product-img a" role="img" aria-label="Glowing cloud hovering above a blue circuit board"></div>
  <div class="product-head">
    <span class="product-icon"><svg width="28" height="22" viewBox="0 0 28 22"><path d="M8 18h13a5 5 0 0 0 0-10 7 7 0 0 0-13-1A5.5 5.5 0 0 0 8 18z" fill="none" stroke="#fff" stroke-width="1.8"/><path d="M11 13l3-3 3 3M14 10v7" stroke="#fff" stroke-width="1.6" fill="none"/></svg></span>
    <span class="product-name">QR.KA CloudSync</span>
  </div>
  <p class="product-text">A seamless cloud integration tool that ensures real-time data synchronization between on-premise and cloud environments.</p>
  <span class="product-line" style="width:302px"></span>
</article>
<article class="product" style="left:445px">
  <div class="product-img b" role="img" aria-label="Hand holding a glowing network security emblem"></div>
  <div class="product-head">
    <span class="product-icon"><svg width="24" height="27" viewBox="0 0 24 27"><path d="M12 2l9 3.5v7c0 6-4 10-9 12.5C7 22.5 3 18.5 3 12.5v-7z" fill="none" stroke="#fff" stroke-width="1.8"/><rect x="8.5" y="12" width="7" height="6" rx="1" fill="#fff"/><path d="M9.5 12v-2a2.5 2.5 0 0 1 5 0v2" fill="none" stroke="#fff" stroke-width="1.6"/></svg></span>
    <span class="product-name">QR.KA SecureOps</span>
  </div>
  <p class="product-text">A security and operations automation platform for monitoring, compliance, and threat detection.</p>
  <span class="product-line" style="width:144px"></span>
</article>
<article class="product" style="left:779px">
  <div class="product-img c" role="img" aria-label="Hands typing on a laptop with translucent AI interface overlays"></div>
  <div class="product-head">
    <span class="product-icon"><svg width="26" height="26" viewBox="0 0 26 26"><rect x="6" y="6" width="14" height="14" rx="2" fill="none" stroke="#fff" stroke-width="1.8"/><rect x="10" y="10" width="6" height="6" fill="#fff"/><path d="M10 2v4M16 2v4M10 20v4M16 20v4M2 10h4M2 16h4M20 10h4M20 16h4" stroke="#fff" stroke-width="1.6"/></svg></span>
    <span class="product-name">QR.KA AI Assist</span>
  </div>
  <p class="product-text">Designing and implementing digital transformation initiatives, including agile methodologies and DevOps practices.</p>
  <span class="product-line" style="width:152px"></span>
</article>

<section class="about">
  <div class="about-photo" role="img" aria-label="Team of colleagues gathered around a laptop at an office desk"></div>
  <svg class="about-cap" width="1200" height="110" viewBox="0 0 1200 110">
    <path d="M0 0 H1200 V110 Q600 -40 0 110Z" fill="#fff"/>
    <path d="M110 72 Q600 -20 1090 72" fill="none" stroke="var(--blue)" stroke-width="7"/>
  </svg>
  <h2>About Us</h2>
  <div class="about-copy">
    <p>At QR.KA Horizon, we bridge the gap between software engineering and IT, creating innovative and seamlessly integrated solutions. Our expertise ensures that businesses benefit from software that is powerful, scalable, and adaptable to existing IT landscapes. We believe in the power of imagination and technology—not just developing software, but crafting future-ready solutions that drive efficiency, security, and automation.</p>
    <p>Our approach combines cutting-edge engineering with a deep understanding of IT infrastructure, allowing organizations to innovate without disruption. In today's fast-paced digital landscape, businesses require software that is not only innovative but also compatible with their evolving IT environments. That's where we come in.</p>
  </div>
  <a class="btn-dark" href="#">Read More</a>
</section>

<section class="testimonials">
  <h2 class="section-title">Our <span class="accent">Testimonials</span></h2>
  <div class="quote" style="left:112px">
    <div class="stars">★★★★★</div>
    <p>Excepteur sint occaecat cupidatat non proident, sunt in culpa qui officia deserunt mollit anim id est laborum.</p>
    <h4>Halvorsen</h4><time>Apr 04 2025</time>
  </div>
  <div class="quote featured" style="left:441px">
    <div class="stars">★★★★★</div>
    <p>Excepteur sint occaecat cupidatat non proident, sunt in culpa qui officia deserunt mollit anim id est laborum.</p>
    <h4>Lenora</h4><time>Apr 04 2025</time>
  </div>
  <div class="quote" style="left:770px">
    <div class="stars">★★★★★</div>
    <p>Excepteur sint occaecat cupidatat non proident, sunt in culpa qui officia deserunt mollit anim id est laborum.</p>
    <h4>Rosalind</h4><time>Apr 04 2025</time>
  </div>
  <div class="t-dots"><i></i><i></i><i></i></div>
  <svg class="t-wave" width="1200" height="130" viewBox="0 0 1200 130">
    <path d="M0 0 H1200 V20 Q600 190 0 20Z" fill="var(--grey-bg)"/>
    <path d="M0 20 Q600 190 1200 20 V130 H0Z" fill="#fff"/>
    <path d="M110 42 Q600 145 1090 42" fill="none" stroke="var(--blue)" stroke-width="6"/>
  </svg>
</section>

<h2 class="solutions-title">Our <span class="accent">Solutions</span></h2>
<p class="solutions-sub">Smart Solutions for Seamless IT Integration</p>
<p class="solutions-copy">At QR.KA Horizon, we develop cutting-edge solutions that bridge the gap between software engineering and IT. Our products are designed to be scalable, secure, and effortlessly integrated, empowering businesses with automation, efficiency, and innovation. Our expertise in software engineering and IT enables us to create scalable, secure, and high-performance solutions tailored to enterprise needs.</p>
<a class="btn btn-sol" href="#">Read More</a>
<div class="sol-photo" role="img" aria-label="Colleagues working together at laptops in a bright loft office"></div>

<footer class="footer">
  <svg class="footer-cap" width="1200" height="100" viewBox="0 0 1200 100">
    <path d="M0 0 H1200 V100 Q600 -30 0 100Z" fill="#fff"/>
    <path d="M110 70 Q600 -10 1090 70" fill="none" stroke="var(--blue)" stroke-width="7"/>
  </svg>
  <div class="footer-brand"><span class="brand-mark"></span>QR.KA HORIZON</div>

  <div class="fcol" style="left:112px;width:300px">
    <h3>Our Mission</h3>
    <p>Our mission is to seamlessly connect these worlds, delivering software solutions that are powerful, scalable, and effortlessly integrated into existing IT infrastructures.</p>
  </div>
  <div class="social">
    <a href="#">Friendloop</a><a href="#">Snapgrid</a><a href="#">Linkwork</a><a href="#">Chirpline</a>
  </div>

  <div class="fcol links" style="left:483px">
    <h3>Main Links</h3>
    <a href="#">Home</a><a href="#">Solutions</a><a href="#">Who We Are</a><a href="#">Contact</a>
  </div>

  <div class="fcol" style="left:680px;width:250px">
    <h3>Contact Us</h3>
    <div class="contact-row">
      <svg width="18" height="22" viewBox="0 0 18 22"><path d="M9 21s7-7 7-12A7 7 0 0 0 2 9c0 5 7 12 7 12z" fill="none" stroke="#fff" stroke-width="1.5"/><circle cx="9" cy="9" r="2.5" fill="none" stroke="#fff" stroke-width="1.5"/></svg>
      <p>48 Meridian Lane, Suite 12, Northfield 20417.</p>
    </div>
    <div class="contact-row">
      <svg width="18" height="18" viewBox="0 0 18 18"><path d="M4 1l3 4-2 2c1 2 3 4 5 5l2-2 4 3-2 3C8 16 2 10 1 4z" fill="none" stroke="#fff" stroke-width="1.4"/></svg>
      <p>+ 1 555 014 2290</p>
    </div>
    <div class="contact-row">
      <svg width="18" height="14" viewBox="0 0 18 14"><rect x="1" y="1" width="16" height="12" fill="none" stroke="#fff" stroke-width="1.4"/><path d="M1 1l8 7 8-7" fill="none" stroke="#fff" stroke-width="1.4"/></svg>
      <p>info@qrkahorizon.example</p>
    </div>
  </div>

  <div class="fcol links" style="left:981px">
    <h3>Other Links</h3>
    <a href="#">Testimonials</a><a href="#">Privacy Policy</a><a href="#">Terms of Use</a><a href="#">Impressum</a>
  </div>

  <div class="rule"></div>
  <p class="copyright">Copyright © 2025 QR.KA Horizon. All rights reserved.</p>
</footer>

</body>
</html>
```